Every Shelf Set Neatly or ESN Organized needs a business card design. ESN Organized is a professi

We need a business card design that is clean, sharp and conveys a sense of organization. I already have a logo.

Target Market(s)

Families (specifically mothers), small business owners, parents, seniors

Industry/Entity Type

Business

Contact Information for Business Card

My website is www.esnorganized-example.com and my Facebook page is http://www.sociallink-example.com/everyshelfsetneatly. The phone number is 418-552-7094 and I want to be listed as Lorna M. Pelham, Owner

Requirements
Must have
• My logo.

```html
<!DOCTYPE html>
<html lang="en">
<head>
<meta charset="UTF-8">
<title>ESN Organized – Business Card</title>
<link href="https://fonts.googleapis.com/css2?family=Montserrat:wght@400;500&family=Open+Sans:ital,wght@0,400;0,600;1,400&display=swap" rel="stylesheet">
<style>
  :root {
    --backdrop: #9b9b9b;
    --brand-blue: #1270c4;
    --paper-white: #e9eaec;
    --card-black: #000000;
    --ink-dark: #1a1a1a;
    --text-light: #f2f5f9;
    --divider: #1c2a38;
  }
  * { margin: 0; padding: 0; box-sizing: border-box; }
  html, body {
    width: 1105px;
    height: 1200px;
    overflow: hidden;
    background: var(--backdrop);
  }
  .canvas {
    position: relative;
    width: 1105px;
    height: 1200px;
  }
  .card {
    position: absolute;
    left: 182px;
    width: 746px;
    height: 427px;
    overflow: hidden;
  }
  .card--front { top: 119px; display: flex; }
  .card--back { top: 638px; background: var(--card-black); }

  /* Front: contact panel */
  .contact-panel {
    width: 352px;
    height: 100%;
    background: var(--brand-blue);
    border-right: 3px solid var(--divider);
    padding: 0 0 0 53px;
    color: var(--text-light);
    font-family: "Open Sans", sans-serif;
  }
  .owner-name {
    margin-top: 121px;
    font-size: 24px;
    font-weight: 600;
    letter-spacing: 0.2px;
    line-height: 1.2;
  }
  .owner-title {
    margin-top: 2px;
    font-size: 18px;
    font-weight: 400;
    line-height: 1.2;
  }
  .contact-list {
    list-style: none;
    margin-top: 33px;
  }
  .contact-item {
    display: flex;
    align-items: center;
    height: 28.5px;
    font-size: 19px;
    line-height: 1;
  }
  .contact-icon {
    width: 18px;
    height: 18px;
    margin-left: 8px;
    margin-right: 9px;
    flex: none;
  }

  /* Front: brand panel */
  .brand-panel {
    flex: 1;
    height: 100%;
    background: var(--paper-white);
    display: flex;
    align-items: center;
    justify-content: center;
  }
  .brand-name {
    font-family: "Montserrat", sans-serif;
    font-weight: 500;
    font-size: 25px;
    letter-spacing: 1.5px;
    color: var(--ink-dark);
    margin-top: -10px;
  }

  /* Back */
  .back-mark {
    position: absolute;
    top: 100px;
    left: 0;
    width: 100%;
    text-align: center;
    font-family: "Montserrat", sans-serif;
    font-weight: 400;
    font-size: 132px;
    line-height: 1;
    letter-spacing: 6px;
    color: var(--brand-blue);
  }
  .back-url {
    position: absolute;
    top: 350px;
    left: 0;
    width: 100%;
    text-align: center;
    font-family: "Open Sans", sans-serif;
    font-style: italic;
    font-size: 19px;
    letter-spacing: 4.5px;
    color: var(--text-light);
  }
</style>
</head>
<body>
<main class="canvas">
  <section class="card card--front" aria-label="Business card front">
    <div class="contact-panel">
      <h1 class="owner-name">LORNA M. PELHAM</h1>
      <p class="owner-title">OWNER</p>
      <ul class="contact-list">
        <li class="contact-item">
          <svg class="contact-icon" viewBox="0 0 24 24" aria-hidden="true">
            <path fill="currentColor" d="M6.6 10.8a15.1 15.1 0 0 0 6.6 6.6l2.2-2.2a1 1 0 0 1 1-.25 11.4 11.4 0 0 0 3.6.57 1 1 0 0 1 1 1V20a1 1 0 0 1-1 1A17 17 0 0 1 3 4a1 1 0 0 1 1-1h3.5a1 1 0 0 1 1 1c0 1.25.2 2.46.57 3.6a1 1 0 0 1-.25 1z"/>
          </svg>
          <span>418-552-7094</span>
        </li>
        <li class="contact-item">
          <svg class="contact-icon" viewBox="0 0 24 24" aria-hidden="true">
            <circle cx="12" cy="12" r="10" fill="currentColor"/>
            <path d="M2 12h20M12 2c3 3 3 17 0 20M12 2c-3 3-3 17 0 20" stroke="#1270c4" stroke-width="1.4" fill="none"/>
          </svg>
          <span>www.esnorganized-example.com</span>
        </li>
        <li class="contact-item">
          <svg class="contact-icon" viewBox="0 0 24 24" aria-hidden="true">
            <rect x="2" y="2" width="20" height="20" rx="2" fill="currentColor"/>
          </svg>
          <span>everyshelfsetneatly</span>
        </li>
      </ul>
    </div>
    <div class="brand-panel">
      <p class="brand-name">Every Shelf Set Neatly</p>
    </div>
  </section>

  <section class="card card--back" aria-label="Business card back">
    <p class="back-mark">ESN</p>
    <p class="back-url">www.esnorganized-example.com</p>
  </section>
</main>
</body>
</html>
```